Medical Clinic Group Looking for Website Design

We own and operate medical clinics and are looking looking to revamp our website. Our current website is www.brightpathcareclinics.ca We need our website to be more functional, user friendly, and easier to maintain.

```html
<!DOCTYPE html>
<html lang="en">
<head>
<meta charset="utf-8">
<title>BrightPath Care Clinics</title>
<link rel="stylesheet" href="https://fonts.googleapis.com/css2?family=Montserrat:wght@400;500;600;700&display=swap">
<style>
:root{
  --teal:#35d0dc;
  --teal-dark:#1fb7c4;
  --ink:#1d1d1f;
  --body:#4a4a4a;
  --muted:#8a8a8a;
  --line:#d6d6d6;
  --soft:#eaf4fb;
  --navy:#2f6f9e;
  --footer:#050505;
  --white:#ffffff;
}
*{margin:0;padding:0;box-sizing:border-box}
html,body{width:1200px;height:3597px;overflow:hidden;background:var(--white)}
body{position:relative;font-family:'Montserrat',sans-serif;color:var(--ink)}
.abs{position:absolute}
.accent{color:var(--teal)}
.btn{position:absolute;display:flex;align-items:center;justify-content:center;gap:12px;background:var(--teal);color:var(--white);border-radius:22px;font-size:13px;font-weight:600;letter-spacing:.3px;white-space:nowrap}
.btn::after{content:"›";font-size:16px;line-height:1}

/* header */
.brand{position:absolute;left:111px;top:24px;display:flex;align-items:center;gap:10px;white-space:nowrap}
.brand-dot{width:44px;height:44px;border-radius:50%;border:3px solid var(--teal);flex:none}
.brand-name{font-size:18px;font-weight:500;color:var(--teal);line-height:1}
.nav-item{position:absolute;top:39px;font-size:12px;color:#333;letter-spacing:.2px;white-space:nowrap}
.nav-item.active{color:var(--teal)}
.nav-item.active::after{content:"";position:absolute;left:0;right:0;top:24px;height:2px;background:var(--teal)}

/* hero */
.hero-title{left:122px;top:152px;font-size:35px;font-weight:600;line-height:57px}
.hero-rule{left:537px;top:172px;width:63px;height:2px;background:var(--teal)}
.hero-copy{left:611px;top:158px;width:490px;font-size:16px;line-height:30px;color:#444}
.slider-num{top:298px;font-size:16px;color:#444}
.slider-track{left:747px;top:307px;width:201px;height:2px;background:var(--line)}
.slider-track span{display:block;width:44px;height:4px;margin-top:-1px;background:var(--teal)}
.photo{position:absolute}

/* about */
.h2{font-size:40px;font-weight:600;white-space:nowrap}
.about-sub{left:128px;top:1025px;font-size:19px;font-weight:500;white-space:nowrap}
.about-copy{left:128px;top:1063px;width:504px;font-size:13.8px;line-height:25px;color:var(--body);text-align:justify}

/* doctors */
.center{left:0;width:1200px;text-align:center}
.card{position:absolute;top:1544px;height:226px;background:var(--white);border-radius:8px;box-shadow:0 4px 18px rgba(0,0,0,.12)}
.card-avatar{position:absolute;left:28px;top:-26px;width:56px;height:56px;background:linear-gradient(#d9dde2,#aeb6be);border-radius:2px}
.card-badge{position:absolute;left:99px;top:5px;width:176px;height:22px;border-radius:11px;background:var(--teal);color:var(--white);font-size:8.5px;font-weight:600;display:flex;align-items:center;justify-content:center;letter-spacing:.3px}
.card-text{position:absolute;left:27px;top:40px;width:258px;font-size:12.5px;line-height:23px;color:#777}
.card-rule{position:absolute;left:27px;right:27px;top:163px;height:1px;background:#e5e5e5}
.card-name{position:absolute;left:27px;top:172px;font-size:15px;font-weight:500;color:#2b6f9a;white-space:nowrap}
.card-role{position:absolute;left:27px;top:196px;font-size:12px;color:#333;white-space:nowrap}
.card-stars{position:absolute;right:16px;top:173px;color:#f7b500;font-size:15px;letter-spacing:-1px}
.card.faded{opacity:.35}
.dots{left:575px;top:1807px;display:flex;gap:4px}
.dots i{display:block;width:6px;height:5px;border-radius:3px;background:#bfeff3}
.dots i.on{width:16px;background:var(--teal)}

/* quick tiles */
.band{left:0;top:1899px;width:1200px;height:244px;background:var(--teal)}
.tile{position:absolute;top:1955px;width:146px;height:132px;background:var(--white);border-radius:4px;display:flex;flex-direction:column;align-items:center;justify-content:flex-end;padding-bottom:12px;font-size:13px;font-weight:500;text-align:center;line-height:15px}
.tile svg{position:absolute;top:18px;left:50%;margin-left:-30px}

/* simplify */
.simplify-copy{left:579px;top:2283px;width:515px;font-size:13.8px;line-height:25px;color:var(--body);text-align:justify}

/* contact */
.touch{left:0;top:2650px;width:600px;height:560px;background:var(--soft)}
.contact-panel{left:600px;top:2650px;width:600px;height:560px;background:linear-gradient(135deg,#3d7fae,#285e88)}
.field{position:absolute;border:2px solid #b9d6ea;background:var(--white);font-size:12px;color:#444;padding:10px 16px}
.info{position:absolute;left:676px;display:flex;gap:16px;color:var(--white)}
.info-icon{width:52px;height:52px;border-radius:50%;border:2px solid var(--white);display:flex;align-items:center;justify-content:center;flex:none}
.info b{display:block;font-size:13px;font-weight:600;margin-top:6px}
.info p{font-size:13px;line-height:21px}

/* footer */
.footer{left:0;top:3150px;width:1200px;height:447px;background:var(--footer)}
.foot-brand{left:108px;top:3312px;display:flex;align-items:center;gap:10px;white-space:nowrap}
.foot-brand .brand-name{font-size:18px}
.foot-col{position:absolute;top:3283px;color:var(--white)}
.foot-col h4{font-size:16px;font-weight:700;letter-spacing:.3px;white-space:nowrap}
.foot-col h4::after{content:"";display:block;width:50px;height:2px;background:var(--teal);margin-top:12px}
.foot-col ul{list-style:none;margin-top:14px;font-size:12.5px;line-height:26px;font-weight:500;white-space:nowrap}
.foot-rule{left:111px;top:3524px;width:978px;height:1px;background:#333}
.copyright{top:3548px;font-size:13px;color:var(--white)}
.to-top{left:1110px;top:3486px;width:46px;height:46px;border-radius:50%;background:var(--teal);display:flex;align-items:center;justify-content:center}
</style>
</head>
<body>

<header>
  <div class="brand"><span class="brand-dot"></span><span class="brand-name">BrightPath Care Clinics</span></div>
  <nav>
    <span class="nav-item active" style="left:406px">HOME</span>
    <span class="nav-item" style="left:489px">LOCATIONS</span>
    <span class="nav-item" style="left:605px">FOR PATIENTS</span>
    <span class="nav-item" style="left:734px">FOR PROVIDERS</span>
    <span class="nav-item" style="left:873px">ABOUT US</span>
  </nav>
  <a class="btn" style="left:960px;top:26px;width:157px;height:40px">BOOK ONLINE</a>
</header>

<section class="hero">
  <h1 class="abs hero-title">Online appointment<br><span class="accent">booking now</span> available to<br>all patients</h1>
  <div class="abs hero-rule"></div>
  <p class="abs hero-copy">BrightPath Care Clinics continues to create options that better suit your lifestyle. Book your appointment when it's convenient for you, even if you don't have a family doctor.</p>
  <span class="abs slider-num" style="left:712px">01</span>
  <div class="abs slider-track"><span></span></div>
  <span class="abs slider-num" style="left:966px">04</span>
  <div class="photo" role="img" aria-label="Photo of a smiling receptionist on the phone at a bright office desk" style="left:111px;top:391px;width:978px;height:492px;background:linear-gradient(120deg,#d9d6cf 0%,#efe7df 45%,#e9c9b8 65%,#c9b7a2 100%)"></div>
  <div class="photo" role="img" aria-label="Next slide photo of an office" style="left:1117px;top:391px;width:83px;height:492px;background:linear-gradient(#e8e4dc,#c8bfb2)"></div>
</section>

<section class="about">
  <h2 class="abs h2" style="left:128px;top:965px">About <span class="accent">Us</span></h2>
  <p class="abs about-sub">Family Doctor - Full Time, Cedar Point Medical Clinic</p>
  <p class="abs about-copy">BrightPath Care Clinics was founded on the idea that a healthy work/life balance is essential to preventing administrative burnout and fatigue for healthcare providers in today's increasingly complex healthcare environment. We believe that the best patient outcomes are acheived when healthcare providers have the time to focus on friends, family and the pursuit of their passions away from their practice. We create the space for that to be possible</p>
  <a class="btn" style="left:128px;top:1251px;width:155px;height:40px">BOOK ONLINE</a>
  <div class="abs" role="img" aria-label="Decorative brand emblem area" style="left:750px;top:1000px;width:272px;height:272px;border-radius:50%;background:radial-gradient(circle,#e6f8fa,#c9d3db)"></div>
</section>

<section class="doctors">
  <h2 class="abs h2 center" style="top:1375px">Top-rated <span class="accent">primary care doctors</span></h2>
  <p class="abs center" style="top:1444px;font-size:19px;font-weight:500">90% of patients gave these primary care doctors 5 stars</p>

  <div class="card faded" style="left:-224px;width:310px"><div class="card-stars">★★★★★</div></div>

  <div class="card" style="left:111px;width:311px">
    <div class="card-avatar" role="img" aria-label="Doctor portrait"></div>
    <div class="card-badge">HIGHLY RECOMMENDED</div>
    <p class="card-text">Saerspiciatis unde omnis iste natus error sitvolup tatem accusan tiumdol oremque laudantiumotam rem aperiameaque ipaefdsa quae abillo inventore veritatiset.</p>
    <div class="card-rule"></div>
    <div class="card-name">Aren Holloway, MD</div>
    <div class="card-role">Internist, Primary Care Doctor</div>
    <div class="card-stars">★★★★★</div>
  </div>
  <div class="card" style="left:446px;width:310px">
    <div class="card-avatar" role="img" aria-label="Doctor portrait"></div>
    <div class="card-badge">HIGHLY RECOMMENDED</div>
    <p class="card-text">Saerspiciatis unde omnis iste natus error sitvolup tatem accusan tiumdol oremque laudantiumotam rem aperiameaque ipaefdsa quae abillo inventore veritatiset.</p>
    <div class="card-rule"></div>
    <div class="card-name">Maya Ellison, MD</div>
    <div class="card-role">Internist, Primary Care Doctor</div>
    <div class="card-stars">★★★★★</div>
  </div>
  <div class="card" style="left:781px;width:310px">
    <div class="card-avatar" role="img" aria-label="Doctor portrait"></div>
    <div class="card-badge">HIGHLY RECOMMENDED</div>
    <p class="card-text">Saerspiciatis unde omnis iste natus error sitvolup tatem accusan tiumdol oremque laudantiumotam rem aperiameaque ipaefdsa quae abillo inventore veritatiset.</p>
    <div class="card-rule"></div>
    <div class="card-name">Tomas Reyva MD</div>
    <div class="card-role">Internist, Primary Care Doctor</div>
    <div class="card-stars">★★★★★</div>
  </div>
  <div class="card faded" style="left:1116px;width:310px">
    <div class="card-avatar" role="img" aria-label="Doctor portrait"></div>
    <p class="card-text">Saerspiciatis unde omnis iste natus error sitvolup tatem accusan tiumdol oremque laudantiumotam rem aperiameaque ipaefdsa quae abillo inventore veritatiset.</p>
    <div class="card-name">Lena Marsh, MD</div>
    <div class="card-role">Internist, Primary Care Doctor</div>
  </div>
  <div class="abs dots"><i></i><i></i><i></i><i class="on"></i><i></i></div>
</section>

<section class="quick">
  <div class="abs band"></div>
  <div class="tile" style="left:111px">
    <svg width="60" height="64" viewBox="0 0 60 64" fill="none" stroke="#222" stroke-width="2"><rect x="16" y="6" width="30" height="26" rx="3"/><path d="M27 6V2h8v4M31 13v12M25 19h12" stroke="#35d0dc"/><path d="M8 40h12l10 4h12M8 54l14-3 20 2 12-9"/><rect x="4" y="38" width="6" height="20"/></svg>
    Find a Provider</div>
  <div class="tile" style="left:278px">
    <svg width="60" height="64" viewBox="0 0 60 64" fill="none" stroke="#222" stroke-width="2"><path d="M16 12l3 6 6 1-4 4 1 6-6-3-5 3 1-6-4-4 6-1zM30 6l3 6 6 1-4 4 1 6-6-3-5 3 1-6-4-4 6-1zM44 12l3 6 6 1-4 4 1 6-6-3-5 3 1-6-4-4 6-1z" stroke="#35d0dc"/><path d="M6 42h10l12 4h10l14-8M6 56l14-4 20 2"/></svg>
    Services</div>
  <div class="tile" style="left:444px">
    <svg width="60" height="64" viewBox="0 0 60 64" fill="none" stroke="#222" stroke-width="2"><rect x="8" y="8" width="40" height="44" rx="3"/><path d="M8 18h40M18 4v8M38 4v8M16 28h8M28 28h8M16 38h8"/><circle cx="46" cy="50" r="10" stroke="#35d0dc"/><path d="M41 50l4 4 6-7" stroke="#35d0dc"/></svg>
    Book an<br>Appointment</div>
  <div class="tile" style="left:610px">
    <svg width="60" height="64" viewBox="0 0 60 64" fill="none" stroke="#222" stroke-width="2"><path d="M30 48S16 32 16 22a14 14 0 0128 0c0 10-14 26-14 26z"/><circle cx="30" cy="22" r="5" stroke="#35d0dc"/><path d="M18 42c-8 2-12 5-12 8 0 5 11 8 24 8s24-3 24-8c0-3-4-6-12-8"/></svg>
    Locations</div>
  <div class="tile" style="left:777px">
    <svg width="60" height="64" viewBox="0 0 60 64" fill="none" stroke="#222" stroke-width="2"><circle cx="26" cy="16" r="10"/><path d="M8 58c0-14 8-22 18-22s18 8 18 22z"/><circle cx="44" cy="44" r="9" stroke="#35d0dc"/><path d="M44 39v10M39 44h10" stroke="#35d0dc"/></svg>
    Patient Resources</div>
  <div class="tile" style="left:943px">
    <svg width="60" height="64" viewBox="0 0 60 64" fill="none" stroke="#222" stroke-width="2"><path d="M14 10l8-2 5 12-5 4c3 7 8 12 15 15l4-5 12 5-2 8c-18 2-39-19-37-37z"/><path d="M34 8a18 18 0 0116 16M34 16a10 10 0 018 8" stroke="#35d0dc"/></svg>
    Contact Us</div>
</section>

<section class="simplify">
  <div class="photo" role="img" aria-label="Photo of a doctor showing a tablet to an elderly patient in a hospital bed" style="left:0;top:2143px;width:590px;height:507px;background:linear-gradient(110deg,#3b6fb0 0%,#9fb6cc 35%,#e8edf1 65%,#ffffff 100%)"></div>
  <h2 class="abs h2" style="left:579px;top:2218px">We Simplify <span class="accent">Providing Care</span></h2>
  <p class="abs simplify-copy">Through our years of experience working with healthcare providers, we have developed customizable practice management solutions that are proven to substantially reduce practice overhead and administrative burden; increase provider and patient satisfaction; and remove the added pressure of managing a business and employees. Our ‘turn-key’ solutions offer customizable, full-spectrum operational support and practice management for Family Doctors, Specialists, and Mental Healthcare providers. We also offer many of our services 'à la carte' for those who only need support in a specific area of their practice.</p>
  <a class="btn" style="left:579px;top:2525px;width:155px;height:41px">BOOK ONLINE</a>
</section>

<section class="contact">
  <div class="abs touch"></div>
  <div class="abs contact-panel" role="img" aria-label="Blue tinted photo of a doctor holding a clipboard"></div>
  <h2 class="abs h2" style="left:111px;top:2720px;font-size:39px">Get In <span class="accent">Touch</span></h2>
  <div class="field" style="left:114px;top:2797px;width:202px;height:38px">Your Name*</div>
  <div class="field" style="left:331px;top:2797px;width:202px;height:38px">Last Name*</div>
  <div class="field" style="left:114px;top:2848px;width:202px;height:38px">Email*</div>
  <div class="field" style="left:331px;top:2848px;width:202px;height:38px">Phone*</div>
  <div class="field" style="left:114px;top:2900px;width:419px;height:108px">Leave us a message*</div>
  <a class="btn" style="left:114px;top:3026px;width:155px;height:41px">SUBMIT</a>

  <h2 class="abs h2" style="left:678px;top:2720px;font-size:39px;color:var(--white)">Contact Us</h2>
  <div class="info" style="top:2808px">
    <div class="info-icon"><svg width="22" height="26" viewBox="0 0 22 26" fill="#fff"><path d="M11 0a9 9 0 00-9 9c0 7 9 17 9 17s9-10 9-17a9 9 0 00-9-9zm0 12a3 3 0 110-6 3 3 0 010 6z"/></svg></div>
    <div><b>ADDRESS</b><p>2480 Lakeview Rd #210, Vernon,<br>BC V1T 4K2, Canada</p></div>
  </div>
  <div class="info" style="top:2893px">
    <div class="info-icon"><svg width="22" height="22" viewBox="0 0 24 24" fill="none" stroke="#fff" stroke-width="2"><path d="M5 3l4-1 2 6-3 2c2 4 4 6 8 8l2-3 6 2-1 4C12 22 2 12 5 3z"/></svg></div>
    <div><b>PHONE</b><p>250.555.0193</p></div>
  </div>
  <div class="info" style="top:2973px">
    <div class="info-icon"><svg width="26" height="26" viewBox="0 0 26 26" fill="none" stroke="#fff" stroke-width="1.8"><circle cx="13" cy="13" r="11"/><ellipse cx="13" cy="13" rx="5" ry="11"/><path d="M2 13h22M4 7h18M4 19h18"/></svg></div>
    <div><b>EMAIL</b><p>hello@brightpathcareclinics.ca</p></div>
  </div>
</section>

<footer>
  <div class="abs footer"></div>
  <svg class="abs" style="left:0;top:3090px" width="1200" height="110" viewBox="0 0 1200 110" preserveAspectRatio="none">
    <path d="M0 65C300 110 700 110 1200 0V110H0z" fill="#050505"/>
    <path d="M0 65C300 104 700 104 1200 0V12C700 112 300 112 0 72z" fill="#35d0dc"/>
  </svg>
  <div class="abs foot-brand">
    <span class="brand-dot" style="width:46px;height:46px"></span>
    <span class="brand-name">BrightPath Care Clinics</span>
  </div>
  <div class="foot-col" style="left:422px"><h4>QUICK LINKS</h4><ul><li>HOME</li><li>LOCATIONS</li><li>FOR PATIENTS</li><li>FOR PROVIDERS</li><li>ABOUT US</li><li>BOOK NOW</li></ul></div>
  <div class="foot-col" style="left:606px"><h4>GET CONNECTED</h4><ul><li>FAQ'S</li><li>TERMS &amp; CONDITIONS</li><li>PRIVACY POLICY</li><li>SITE MAP</li><li>COOKIES POLICY</li></ul></div>
  <div class="foot-col" style="left:829px"><h4>LINKS</h4><ul><li>COPYRIGHT</li><li>LEGAL</li><li>PRIVACY</li><li>ACCESSIBILITY</li><li>SITEMAP</li></ul></div>
  <div class="foot-col" style="left:1002px"><h4>SUPPORT</h4><ul><li>TEAM</li><li>ABOUT US</li><li>CAREERS</li><li>OUR VALUES</li></ul></div>
  <div class="abs to-top"><svg width="16" height="10" viewBox="0 0 16 10" fill="none" stroke="#fff" stroke-width="2"><path d="M2 8l6-6 6 6"/></svg></div>
  <div class="abs foot-rule"></div>
  <p class="abs copyright center">©2022. BRIGHTPATH CARE CLINICS. ALL RIGHTS RESERVED.</p>
</footer>

</body>
</html>
```